Keystone ridge construction brochure

i would like a brochure that can be send to clients digitally and printed. we are a geotechnical, foundation, and concrete company. I attached info below

Target Market(s)

Construction managers, general contractors, developers, municipalities, private, and commercial partners.

Industry/Entity Type

Geotechnical / foundation

Font styles to use
Serif
Other font styles liked:
• Maybe same as logo

Colors
0054AA
0677BA
7BADD7
CADEEF
E8F1F8

```html
<!DOCTYPE html>
<html lang="en">
<head>
<meta charset="utf-8">
<title>Keystone Ridge Construction Brochure</title>
<link href="https://fonts.googleapis.com/css2?family=Oswald:wght@500;600;700&family=Open+Sans:wght@400;500;600&display=swap" rel="stylesheet">
<style>
  :root {
    --navy: #0b1f4d;
    --blue: #2a56c6;
    --charcoal: #3a3a3c;
    --card: #e9eaec;
    --stage: #dcdcdc;
    --white: #ffffff;
    --ink: #1c1c1e;
  }
  * { box-sizing: border-box; margin: 0; padding: 0; }
  html, body { width: 1200px; height: 800px; overflow: hidden; background: var(--stage); }
  .canvas { position: relative; width: 1200px; height: 800px; }
  .page { position: absolute; top: 70px; width: 510px; height: 660px; background: var(--white); overflow: hidden; font-family: "Open Sans", sans-serif; color: var(--ink); }
  .page--front { left: 63px; }
  .page--back { left: 627px; }
  .abs { position: absolute; }
  .display { font-family: "Oswald", sans-serif; font-weight: 600; text-transform: uppercase; line-height: 1; }
  .accent { color: var(--blue); }
  .wordmark { font-family: "Oswald", sans-serif; font-weight: 700; color: var(--navy); text-align: center; line-height: 0.95; letter-spacing: 1px; }

  /* front */
  .front-art { position: absolute; inset: 0; }
  .front-brand { left: 0; width: 510px; top: 16px; font-size: 27px; }
  .headline { left: 0; width: 510px; top: 84px; text-align: center; font-size: 27.5px; color: var(--navy); }
  .rule { position: absolute; height: 2.5px; }
  .services-line { left: 0; width: 510px; top: 131px; text-align: center; font-size: 12.5px; font-weight: 600; color: var(--navy); letter-spacing: .3px; }
  .services-line .dot { display: inline-block; width: 6px; height: 6px; border-radius: 50%; background: var(--blue); margin: 0 6px 1px 10px; }
  .tagline { left: 70px; width: 370px; top: 151px; text-align: center; font-size: 11px; line-height: 1.3; }
  .how-title { left: 26px; top: 286px; font-size: 21px; color: var(--white); }
  .steps { left: 25px; top: 336px; list-style: none; }
  .step { position: relative; height: 54px; padding-left: 44px; color: var(--white); }
  .step-icon { position: absolute; left: 0; top: 0; width: 32px; height: 32px; border-radius: 50%; background: var(--white); display: flex; align-items: center; justify-content: center; }
  .step-title { font-size: 15px; padding-top: 1px; }
  .step-text { font-size: 8.8px; margin-top: 4px; }
  .front-phone { left: 88px; top: 614px; display: flex; align-items: center; gap: 8px; font-size: 20px; font-weight: 600; color: var(--navy); }
  .phone-badge { width: 29px; height: 29px; border-radius: 50%; background: var(--navy); display: flex; align-items: center; justify-content: center; }

  /* back */
  .top-band { left: 0; top: 0; width: 510px; height: 100px; background: var(--navy); }
  .top-brand { left: 30px; top: 28px; width: 146px; font-size: 22px; color: var(--white); }
  .vline { position: absolute; width: 1px; background: var(--white); }
  .intro { left: 236px; top: 17px; width: 250px; color: var(--white); font-size: 8.3px; line-height: 1.5; }
  .intro p + p { margin-top: 7px; }
  .section-title { left: 0; width: 510px; top: 118px; text-align: center; font-size: 22px; color: var(--navy); }
  .section-title::before, .section-title::after { content: ""; display: inline-block; width: 48px; height: 1.5px; background: var(--navy); vertical-align: middle; margin: 0 6px; }
  .service-card { position: absolute; top: 166px; width: 140px; height: 198px; }
  .service-card .panel { position: absolute; inset: 0 0 93px 0; background: var(--card); }
  .service-card .hex { position: absolute; left: 52px; top: -18px; }
  .service-card h3 { position: absolute; left: 18px; top: 31px; font-size: 11.5px; color: var(--navy); }
  .service-card ul { position: absolute; left: 18px; top: 52px; list-style: none; font-size: 7.3px; line-height: 12.8px; }
  .service-card li::before { content: ""; display: inline-block; width: 4px; height: 4px; border-radius: 50%; background: var(--navy); margin-right: 6px; vertical-align: 1px; }
  .service-card .photo { position: absolute; left: 0; bottom: 0; width: 140px; height: 93px; }
  .mid-band { left: 0; top: 381px; width: 510px; height: 135px; background: var(--navy); color: var(--white); }
  .industries-title { left: 26px; top: 20px; font-size: 15px; }
  .industries { left: 26px; top: 52px; width: 220px; list-style: none; display: grid; grid-template-columns: 103px 110px; row-gap: 8px; font-size: 10.3px; }
  .industries li { display: flex; align-items: center; gap: 6px; }
  .cta-title { left: 281px; top: 19px; font-size: 19.5px; line-height: 1.15; }
  .cta-text { left: 282px; top: 74px; width: 205px; font-size: 7.4px; line-height: 1.6; }
  .bottom-brand { left: 30px; top: 566px; width: 190px; font-size: 29px; }
  .contact-title { left: 263px; top: 535px; font-size: 17px; color: var(--navy); }
  .contacts { left: 263px; top: 566px; list-style: none; font-size: 10.4px; color: var(--navy); }
  .contacts li { display: flex; align-items: center; gap: 8px; height: 20px; }
</style>
</head>
<body>
<div class="canvas">

  <section class="page page--front">
    <svg class="front-art" viewBox="0 0 510 660" width="510" height="660" aria-hidden="false">
      <defs>
        <linearGradient id="rig-tone" x1="0" y1="0" x2="1" y2="1">
          <stop offset="0" stop-color="#a9b6c9"/>
          <stop offset=".5" stop-color="#7c7468"/>
          <stop offset="1" stop-color="#9a7a5c"/>
        </linearGradient>
      </defs>
      <circle cx="454" cy="415" r="247" fill="var(--navy)"/>
      <polygon points="0,172 304,339 406,410 304,491 0,647" fill="var(--charcoal)" stroke="var(--white)" stroke-width="5" stroke-linejoin="round"/>
      <rect x="0" y="160" width="3" height="500" fill="var(--charcoal)"/>
      <circle cx="406" cy="410" r="168" fill="var(--charcoal)"/>
      <circle cx="406" cy="410" r="158" fill="var(--white)"/>
      <circle cx="406" cy="410" r="149" fill="url(#rig-tone)" role="img" aria-label="Photo of a drilling rig boring a foundation pile into the ground"/>
    </svg>

    <div class="abs wordmark front-brand">KEYSTONE<br>RIDGE</div>
    <h1 class="abs display headline">Built on <span class="accent">strength.</span> Engineered <span class="accent">to last.</span></h1>
    <span class="rule" style="left:212px;top:120px;width:51px;background:var(--navy)"></span>
    <span class="rule" style="left:266px;top:120px;width:32px;background:var(--blue)"></span>
    <p class="abs services-line"><span class="dot"></span>GEOTECHNICAL <span class="dot"></span> FOUNDATION <span class="dot"></span> CONCRETE</p>
    <p class="abs tagline">Engineered solutions. Proven performance. Stronger foundations from the ground up.</p>

    <h2 class="abs display how-title">How it works</h2>
    <span class="rule" style="left:27px;top:317px;width:37px;height:2px;background:var(--white)"></span>
    <ul class="abs steps">
      <li class="step">
        <span class="step-icon"><svg width="16" height="16" viewBox="0 0 16 16"><path d="M8 1 L14 3.5 V8 C14 11.5 11 14 8 15 C5 14 2 11.5 2 8 V3.5 Z" fill="none" stroke="var(--navy)" stroke-width="1.5"/><path d="M8 5 V11 M5 8 H11" stroke="var(--blue)" stroke-width="1.6"/></svg></span>
        <h3 class="display step-title">Safety first</h3>
        <p class="step-text">Safety-driven culture on every job.</p>
      </li>
      <li class="step">
        <span class="step-icon"><svg width="16" height="16" viewBox="0 0 16 16"><rect x="2" y="9" width="2.6" height="5" fill="var(--navy)"/><rect x="6.7" y="6" width="2.6" height="8" fill="var(--navy)"/><rect x="11.4" y="3" width="2.6" height="11" fill="var(--blue)"/></svg></span>
        <h3 class="display step-title">Built to perform</h3>
        <p class="step-text">Modern equipment. Experienced teams.</p>
      </li>
      <li class="step">
        <span class="step-icon"><svg width="16" height="16" viewBox="0 0 16 16"><rect x="1.5" y="2" width="11" height="10" rx="1" fill="none" stroke="var(--navy)" stroke-width="1.4"/><circle cx="11.5" cy="11.5" r="3.5" fill="var(--navy)"/><path d="M9.8 11.5 L11 12.7 L13.2 10.4" stroke="var(--white)" stroke-width="1.1" fill="none"/></svg></span>
        <h3 class="display step-title">Engineered solutions</h3>
        <p class="step-text">Smart, practical solutions for every challenge.</p>
      </li>
      <li class="step">
        <span class="step-icon"><svg width="16" height="16" viewBox="0 0 16 16"><circle cx="8" cy="8" r="6.5" fill="none" stroke="var(--navy)" stroke-width="1.4"/><path d="M5 8.2 L7.2 10.4 L11.2 5.8" stroke="var(--blue)" stroke-width="1.6" fill="none"/></svg></span>
        <h3 class="display step-title">Reliable partner</h3>
        <p class="step-text">On-time. On-budget. Every time.</p>
      </li>
    </ul>

    <p class="abs front-phone">
      <span class="phone-badge"><svg width="14" height="14" viewBox="0 0 24 24"><path d="M6.6 10.8a15.1 15.1 0 0 0 6.6 6.6l2.2-2.2a1 1 0 0 1 1-.25 11.4 11.4 0 0 0 3.6.57 1 1 0 0 1 1 1V20a1 1 0 0 1-1 1A17 17 0 0 1 3 4a1 1 0 0 1 1-1h3.5a1 1 0 0 1 1 1c0 1.25.2 2.45.57 3.6a1 1 0 0 1-.25 1z" fill="var(--white)"/></svg></span>
      (555) 014-2280
    </p>
  </section>

  <section class="page page--back">
    <div class="abs top-band">
      <div class="abs wordmark top-brand">KEYSTONE<br>RIDGE</div>
      <span class="vline" style="left:207px;top:19px;height:63px"></span>
      <div class="abs intro">
        <p>Keystone Ridge is a trusted partner in geotechnical, foundation, and concrete construction.</p>
        <p>We deliver engineered solutions that build stronger structures with safety, quality, and integrity.</p>
      </div>
    </div>

    <h2 class="abs display section-title"><span class="accent">Our</span> Services</h2>

    <article class="service-card" style="left:26px">
      <div class="panel"></div>
      <svg class="hex" width="36" height="38" viewBox="0 0 36 38"><polygon points="18,1 34,10 34,28 18,37 2,28 2,10" fill="var(--navy)" stroke="var(--white)" stroke-width="2"/><rect x="11" y="12" width="14" height="12" fill="none" stroke="var(--white)" stroke-width="1.6"/><path d="M14 24 V17 M18 24 V15 M22 24 V19" stroke="var(--white)" stroke-width="1.6"/></svg>
      <h3 class="display">Geotechnical</h3>
      <ul><li>Site Investigation</li><li>Soil Analysis</li><li>Ground Improvement</li><li>Earth Retention Solutions</li></ul>
      <div class="photo" role="img" aria-label="Photo of tracked drilling equipment on excavated soil" style="background:linear-gradient(135deg,#5a4838,#9a6b43 55%,#c79a6c)"></div>
    </article>

    <article class="service-card" style="left:185px">
      <div class="panel"></div>
      <svg class="hex" width="36" height="38" viewBox="0 0 36 38"><polygon points="18,1 34,10 34,28 18,37 2,28 2,10" fill="var(--blue)" stroke="var(--white)" stroke-width="2"/><rect x="10" y="11" width="16" height="4" fill="var(--white)"/><rect x="10" y="17" width="7" height="4" fill="var(--white)"/><rect x="10" y="23" width="7" height="4" fill="var(--white)"/><circle cx="22.5" cy="23" r="4" fill="none" stroke="var(--white)" stroke-width="1.8"/></svg>
      <h3 class="display">Foundation</h3>
      <ul><li>Deep Foundations</li><li>Helical Piles</li><li>Shoring Systems</li><li>Structural Support</li></ul>
      <div class="photo" role="img" aria-label="Photo of stacked steel piles at a construction site with a crane" style="background:linear-gradient(180deg,#b7bcc2,#8b8d8f 45%,#4e4a46)"></div>
    </article>

    <article class="service-card" style="left:344px">
      <div class="panel"></div>
      <svg class="hex" width="36" height="38" viewBox="0 0 36 38"><polygon points="18,1 34,10 34,28 18,37 2,28 2,10" fill="#8a8c90" stroke="var(--white)" stroke-width="2"/><rect x="10" y="13" width="9" height="8" fill="var(--white)"/><rect x="19" y="17" width="7" height="4" fill="var(--white)"/><circle cx="13" cy="24" r="2.4" fill="var(--white)"/><circle cx="23" cy="24" r="2.4" fill="var(--white)"/></svg>
      <h3 class="display">Concrete</h3>
      <ul><li>Structural Concrete</li><li>Foundations &amp; Slabs</li><li>Reinforced Concrete</li><li>Commercial &amp; Industrial Work</li></ul>
      <div class="photo" role="img" aria-label="Photo of a worker pouring concrete over steel reinforcement mesh" style="background:linear-gradient(135deg,#8d8f8c,#b5b4ad 50%,#6f716e)"></div>
    </article>

    <div class="abs mid-band">
      <h2 class="abs display industries-title">Industries <span class="accent">we serve</span></h2>
      <span class="rule" style="left:26px;top:40px;width:34px;height:2px;background:var(--blue)"></span>
      <ul class="abs industries">
        <li><svg width="11" height="11" viewBox="0 0 12 12"><circle cx="6" cy="6" r="5" fill="none" stroke="var(--blue)" stroke-width="1"/><path d="M3.5 6 L5.4 7.9 L9.5 3.5" fill="none" stroke="var(--blue)" stroke-width="1.2"/></svg>Commercial</li>
        <li><svg width="11" height="11" viewBox="0 0 12 12"><circle cx="6" cy="6" r="5" fill="none" stroke="var(--blue)" stroke-width="1"/><path d="M3.5 6 L5.4 7.9 L9.5 3.5" fill="none" stroke="var(--blue)" stroke-width="1.2"/></svg>Institutional</li>
        <li><svg width="11" height="11" viewBox="0 0 12 12"><circle cx="6" cy="6" r="5" fill="none" stroke="var(--blue)" stroke-width="1"/><path d="M3.5 6 L5.4 7.9 L9.5 3.5" fill="none" stroke="var(--blue)" stroke-width="1.2"/></svg>Industrial</li>
        <li><svg width="11" height="11" viewBox="0 0 12 12"><circle cx="6" cy="6" r="5" fill="none" stroke="var(--blue)" stroke-width="1"/><path d="M3.5 6 L5.4 7.9 L9.5 3.5" fill="none" stroke="var(--blue)" stroke-width="1.2"/></svg>Energy</li>
        <li><svg width="11" height="11" viewBox="0 0 12 12"><circle cx="6" cy="6" r="5" fill="none" stroke="var(--blue)" stroke-width="1"/><path d="M3.5 6 L5.4 7.9 L9.5 3.5" fill="none" stroke="var(--blue)" stroke-width="1.2"/></svg>Infrastructure</li>
        <li><svg width="11" height="11" viewBox="0 0 12 12"><circle cx="6" cy="6" r="5" fill="none" stroke="var(--blue)" stroke-width="1"/><path d="M3.5 6 L5.4 7.9 L9.5 3.5" fill="none" stroke="var(--blue)" stroke-width="1.2"/></svg>Public Works</li>
      </ul>
      <span class="vline" style="left:255px;top:22px;height:89px"></span>
      <h2 class="abs display cta-title">Let's build<br><span class="accent">something solid.</span></h2>
      <p class="abs cta-text">From complex geotechnical challenges to large-scale concrete construction, Keystone Ridge delivers solutions you can build on.</p>
    </div>

    <div class="abs wordmark bottom-brand">KEYSTONE<br>RIDGE</div>

    <h2 class="abs display contact-title">Contact <span class="accent">us</span></h2>
    <span class="rule" style="left:263px;top:558px;width:33px;height:2px;background:var(--blue)"></span>
    <ul class="abs contacts">
      <li><svg width="11" height="11" viewBox="0 0 24 24"><path d="M6.6 10.8a15.1 15.1 0 0 0 6.6 6.6l2.2-2.2a1 1 0 0 1 1-.25 11.4 11.4 0 0 0 3.6.57 1 1 0 0 1 1 1V20a1 1 0 0 1-1 1A17 17 0 0 1 3 4a1 1 0 0 1 1-1h3.5a1 1 0 0 1 1 1c0 1.25.2 2.45.57 3.6a1 1 0 0 1-.25 1z" fill="var(--blue)"/></svg>(555) 014-2280</li>
      <li><svg width="11" height="11" viewBox="0 0 24 24"><rect x="2" y="5" width="20" height="14" rx="1" fill="var(--blue)"/><path d="M2 6 L12 13 L22 6" fill="none" stroke="var(--white)" stroke-width="1.6"/></svg>info@keystoneridge.com</li>
      <li><svg width="11" height="11" viewBox="0 0 24 24"><circle cx="12" cy="12" r="9.5" fill="none" stroke="var(--blue)" stroke-width="2"/><ellipse cx="12" cy="12" rx="4" ry="9.5" fill="none" stroke="var(--blue)" stroke-width="1.6"/><path d="M2.5 12 H21.5" stroke="var(--blue)" stroke-width="1.6"/></svg>www.keystoneridge.com</li>
      <li><svg width="11" height="11" viewBox="0 0 24 24"><path d="M12 2a7 7 0 0 0-7 7c0 5 7 13 7 13s7-8 7-13a7 7 0 0 0-7-7z" fill="var(--blue)"/><circle cx="12" cy="9" r="2.6" fill="var(--white)"/></svg>48 Bedrock Lane Fairview, USA 54321</li>
    </ul>
  </section>

</div>
</body>
</html>
```